Webshop Template

For our Webstore in UK we need a complete Template,
shoppingcart is Magento, the Shop is focussed on Download software,

the name: Kelvoramarket.co.uk

Check out some other good stores, like zandrilo.de
Updates

for example the Page from 

www.brunt.co.uk or

www.zandrilo.de

www.mokvelta.de

www.quarnepreis.de

The Logodesign which are in Consideration

http://www.plimvector.com/design/5520913/logo-design-by-tomek7ga

http://www.plimvector.com/design/5518207/logo-design-by-ivanoralba

http://www.plimvector.com/design/5517346/logo-design-by-granite-fables

http://www.plimvector.com/design/5516085/logo-design-by-quillotaste

http://www.plimvector.com/design/5515472/logo-design-by-tuvaro

http://www.plimvector.com/design/5514619/logo-design-by-lone-pine-graphic-

Target Market(s)

B2C - Consumer Marcet

Industry/Entity Type

Shop

```html
<!DOCTYPE html>
<html lang="en">
<head>
<meta charset="utf-8">
<title>Kelvoramarket.co.uk – Top 10 Apps</title>
<link href="https://fonts.googleapis.com/css2?family=Oswald:wght@400;500&family=Arimo:wght@400;700&display=swap" rel="stylesheet">
<style>
:root{
  --black:#0b0b0b;
  --panel:#151515;
  --panel-edge:#2a2a2a;
  --pink:#d81f63;
  --pink-dark:#8e0b3c;
  --pink-text:#e0306f;
  --bg-top:#c0124f;
  --bg-mid:#a00f44;
  --bg-low:#5a0a2a;
  --gold:#f7c31a;
  --gold-dark:#e0a500;
  --white:#ffffff;
  --grey:#9a9a9a;
  --grey-dark:#5e5e5e;
  --line:#3a3a3a;
}
*{box-sizing:border-box;margin:0;padding:0}
html,body{width:921px;height:1200px;overflow:hidden}
body{position:relative;font-family:Arimo,Arial,sans-serif;color:var(--white);
  background:linear-gradient(180deg,var(--bg-top) 0,var(--bg-mid) 280px,#7d0c37 650px,var(--bg-low) 930px);}
.abs{position:absolute}
a{color:inherit;text-decoration:none}

/* top bar */
.topbar{left:0;top:0;width:921px;height:27px;background:linear-gradient(#2b2b2b,#000);}
.topbar .welcome{left:116px;top:6px;font:500 12px Oswald,sans-serif;}
.toplinks{right:109px;top:8px;display:flex;font:400 8px Oswald,sans-serif;color:#ccc;letter-spacing:.2px}
.toplinks span{padding:0 10px;border-left:1px solid #777;line-height:10px}
.toplinks span:first-child{border:none}
.toplinks span:last-child{padding-right:0}

.logo{left:116px;top:50px;font:700 29px Arimo,sans-serif;letter-spacing:1px}

.cartbox{left:568px;top:41px;width:244px;height:50px;background:var(--white);border-radius:4px;border:1px solid #ddd;color:#111}
.cartbox .cart-side{position:absolute;left:0;top:0;width:105px;height:100%;border-right:1px solid #ccc;text-align:center}
.cart-icon{position:absolute;left:34px;top:4px;width:38px;height:26px;background:var(--black);display:flex;align-items:center;justify-content:center}
.cart-icon i{width:30px;height:20px;background:var(--pink);border-radius:3px;display:flex;align-items:center;justify-content:center}
.cartbox .count{position:absolute;left:0;width:105px;top:34px;font:700 10px Arimo,sans-serif}
.cartbox .mail{position:absolute;right:12px;top:7px;font:400 12px Oswald,sans-serif;color:var(--pink)}
.cartbox .phone{position:absolute;right:12px;top:23px;font:400 16px Oswald,sans-serif}

/* nav */
.nav{left:108px;top:104px;width:704px;height:49px;background:linear-gradient(#1d1d1d,#050505);border-radius:4px;display:flex}
.nav a{height:49px;display:flex;align-items:center;justify-content:center;font:700 12.5px Arimo,sans-serif;border-right:1px solid #2c2c2c}
.nav .home{width:116px}.nav .top10{width:98px;background:#000}.nav .most{width:114px}.nav .free{width:101px}
.search{left:594px;top:114px;width:174px;height:30px;background:#fff;border-radius:3px;color:#333;font-size:8.5px;padding:10px 10px}
.search-btn{left:770px;top:114px;width:33px;height:30px;background:linear-gradient(var(--gold),var(--gold-dark));border-radius:3px;display:flex;align-items:center;justify-content:center}

.crumb{left:116px;top:172px;font:700 10px Arimo,sans-serif;color:var(--gold)}

/* sidebar */
.sidebar{left:108px;top:199px;width:212px;height:533px;background:linear-gradient(#121212,#0a0a0a);border-radius:4px;box-shadow:0 2px 6px rgba(0,0,0,.5)}
.side-head{position:absolute;left:3px;width:206px;height:28px;border:1px solid #f14e86;background:linear-gradient(#e02868,#b8124f);font:400 11.5px Oswald,sans-serif;padding:6px 14px;text-transform:uppercase}
.side-head.gold{background:linear-gradient(#ffd31e,#f1b700);border-color:#ffe680;color:#222}
.sidebar .lbl{position:absolute;left:18px;font:700 8px Arimo,sans-serif}
.sidebar .price{position:absolute;left:18px;font:400 8px Arimo,sans-serif;color:var(--pink-text);line-height:13px}
.sidebar .co{position:absolute;left:19px;font:700 9px Arimo,sans-serif;color:var(--pink-text)}
.divider{position:absolute;left:18px;width:176px;border-top:1px solid #333}
.sidebar .small{position:absolute;left:18px;font-size:8px;color:var(--grey)}
.sidebar .small b{color:var(--pink-text);text-decoration:underline}
.btn-pink{position:absolute;height:21px;border-radius:5px;background:linear-gradient(#e62a6b,#b0104a);border:1px solid #f5739f;font:400 9.5px Oswald,sans-serif;display:flex;align-items:center;justify-content:center}
.recent-title{position:absolute;left:18px;top:309px;font:700 8px Arimo,sans-serif;color:var(--gold)}
.thumb{position:absolute;left:19px;top:334px;width:42px;height:42px;background:linear-gradient(#f3f3f3,#e6e6e6)}
.recent-name{position:absolute;left:66px;top:336px;font:400 8px Oswald,sans-serif;color:var(--pink-text);line-height:9px}
.recent-qty{position:absolute;left:66px;top:360px;font-size:8px;color:var(--grey)}
.mini-x{position:absolute;width:9px;height:9px;background:#ddd;border:1px solid #999;font:700 7px/7px Arimo,sans-serif;color:#333;text-align:center}
.mini-edit{position:absolute;width:9px;height:9px;background:#f3e58a;border:1px solid #999}
.cmp-item{position:absolute;left:19px;width:180px;height:25px;border-bottom:1px dotted #444;font:700 9px Arimo,sans-serif;color:var(--pink-text);padding:7px 0 0 8px}
.clear{position:absolute;left:19px;top:526px;font:700 8.5px Arimo,sans-serif;color:var(--pink-text)}

/* toolbar */
.toolbar{left:356px;width:454px;height:38px;background:linear-gradient(#1b1b1b,#070707);border-radius:4px;box-shadow:0 2px 5px rgba(0,0,0,.5);font-size:8.5px;color:#bbb}
.toolbar .view{position:absolute;top:0;height:38px;width:28px;display:flex;align-items:center;justify-content:center;border-right:1px solid #333}
.toolbar .sortlbl{position:absolute;left:71px;top:15px}
.select{position:absolute;top:13px;height:12px;background:#fff;color:#111;font-size:8px;padding:1px 3px;border:1px solid #999}
.select i{position:absolute;right:0;top:0;width:10px;height:10px;background:#ddd;border-left:1px solid #999}
.toolbar .arrow{position:absolute;left:175px;top:13px;color:var(--gold);font-size:9px}
.toolbar .show{position:absolute;left:264px;top:15px}
.toolbar .per{position:absolute;left:326px;top:15px}
.toolbar .page{position:absolute;left:384px;top:15px}
.toolbar .p1{position:absolute;left:416px;top:15px;color:var(--gold);text-decoration:underline;font-weight:700}
.toolbar .p2{position:absolute;left:428px;top:15px;color:#ddd;font-weight:700}
.toolbar .next{position:absolute;left:440px;top:14px;color:var(--gold);font-weight:700}

/* product cards */
.card{width:209px;height:281px;background:#fff;border-radius:6px;box-shadow:0 2px 6px rgba(0,0,0,.35);overflow:hidden}
.card .img{position:absolute;left:22px;top:22px;width:165px;height:165px;background:linear-gradient(#f6f6f6,#ececec)}
.card .title{position:absolute;left:0;width:100%;top:199px;text-align:center;font:400 11px Oswald,sans-serif;color:var(--pink)}
.card .bar{position:absolute;left:0;top:217px;width:100%;height:34px;background:linear-gradient(#1d1d1d,#000)}
.card .price{position:absolute;left:12px;top:7px;font:400 16px Oswald,sans-serif}
.card .add{position:absolute;right:11px;top:7px;width:30px;height:20px;border-radius:4px;background:linear-gradient(#ec2f70,#b80f4d);border:1px solid #f589ae;display:flex;align-items:center;justify-content:center}
.card .links{position:absolute;top:260px;font:400 8.5px Oswald,sans-serif;color:#444}

/* footer */
.footer{left:0;top:930px;width:921px;height:270px;background:#000}
.fcol{position:absolute;width:160px}
.fcol h4{font:400 11.5px Oswald,sans-serif;text-transform:uppercase;margin-bottom:8px}
.fcol p{font-size:7.6px;line-height:13px;color:#8a8a8a}
.fcol li{list-style:none;font-size:7.8px;color:var(--pink);border-bottom:1px dotted #333;height:20px;padding-top:6px;width:140px}
.fdots{position:absolute;left:108px;top:91px;width:704px;border-top:1px dotted #333}
.newsletter input{display:none}
.nl-field{position:absolute;left:666px;top:125px;width:117px;height:20px;background:linear-gradient(#ddd,#fff);border-radius:2px}
.nl-btn{position:absolute;left:785px;top:125px;width:30px;height:20px;background:linear-gradient(var(--gold),var(--gold-dark));border-radius:2px;display:flex;align-items:center;justify-content:center}
.cards{position:absolute;left:666px;top:180px;display:flex;gap:5px}
.cards i{width:26px;height:16px;border-radius:2px;background:#ddd;border:1px solid #999}
.copyright{position:absolute;left:0;top:228px;width:921px;border-top:1px solid #222;height:42px;background:#0d0d0d;text-align:center;font-size:7.6px;color:#888;padding-top:14px}
</style>
</head>
<body>

<div class="abs topbar">
  <div class="abs welcome">Welcome to our online store!</div>
  <nav class="abs toplinks"><span>MY ACCOUNT</span><span>MY WISHLIST</span><span>MY CART</span><span>CHECKOUT</span><span>LOG IN</span></nav>
</div>

<div class="abs logo">LOGO</div>

<div class="abs cartbox">
  <div class="cart-side">
    <div class="cart-icon"><i><svg width="16" height="12" viewBox="0 0 16 12"><path d="M1 1h2.5l1.8 7h8l1.5-5H4.5" fill="none" stroke="#fff" stroke-width="1.4"/><circle cx="6" cy="10.5" r="1.1" fill="#fff"/><circle cx="12" cy="10.5" r="1.1" fill="#fff"/></svg></i></div>
    <div class="count">1 item in cart</div>
  </div>
  <div class="mail">support@kelvorashop.com</div>
  <div class="phone">08 0011 222 3333</div>
</div>

<nav class="abs nav">
  <a class="home">Home</a><a class="top10">Top 10 Apps</a><a class="most">Most Downloaded</a><a class="free">Freeware</a>
</nav>
<div class="abs search">Search entire store here...</div>
<div class="abs search-btn"><svg width="14" height="14" viewBox="0 0 14 14"><circle cx="6" cy="6" r="4.2" fill="none" stroke="#222" stroke-width="1.6"/><path d="M9 9l4 4" stroke="#222" stroke-width="1.8"/></svg></div>

<div class="abs crumb">Home -&gt; Top 10 Apps</div>

<aside class="abs sidebar">
  <div class="side-head" style="top:11px">Shop By</div>
  <div class="lbl" style="top:56px">Price</div>
  <div class="price" style="top:66px">$100.00 - $200.00 (08)<br>$300.00 - $400.00 (12)<br>$400.00 - $500.00 (08)</div>
  <div class="divider" style="top:106px"></div>
  <div class="lbl" style="top:116px">Company</div>
  <div class="co" style="top:131px">Norvale</div>
  <div class="co" style="top:151px">Pexta</div>
  <div class="co" style="top:171px">Lumira</div>
  <div class="co" style="top:191px">Tandix</div>
  <div class="side-head gold" style="top:201px">My Cart</div>
  <div class="small" style="top:248px">There is <b>1 item</b> in your cart.</div>
  <div class="small" style="top:262px">Cart Subtotal: $149.99</div>
  <div class="btn-pink" style="left:18px;top:275px;width:64px">CHECKOUT</div>
  <div class="recent-title">Recently added item(s)</div>
  <div class="thumb" role="img" aria-label="Product thumbnail"></div>
  <div class="recent-name">SIMPLY DUMMY TEXT OF<br>THE PRINTING</div>
  <div class="recent-qty">1 x $649.99</div>
  <div class="mini-edit" style="left:172px;top:339px"></div>
  <div class="mini-x" style="left:185px;top:339px">×</div>
  <div class="side-head" style="top:403px">Compare Produts</div>
  <div class="cmp-item" style="top:440px">Skylark 8</div>
  <div class="mini-x" style="left:185px;top:446px">×</div>
  <div class="cmp-item" style="top:465px">Skylark 7 Ultimate</div>
  <div class="mini-x" style="left:185px;top:471px">×</div>
  <div class="clear">Clear All</div>
  <div class="btn-pink" style="left:132px;top:499px;width:65px">COMPARE</div>
</aside>

<div class="abs toolbar" style="top:199px">
  <div class="view" style="left:0"><svg width="8" height="8"><g fill="#f7c31a"><rect width="3.5" height="3.5"/><rect x="4.5" width="3.5" height="3.5"/><rect y="4.5" width="3.5" height="3.5"/><rect x="4.5" y="4.5" width="3.5" height="3.5"/></g></svg></div>
  <div class="view" style="left:29px"><svg width="10" height="7"><g fill="#888"><rect width="10" height="1"/><rect y="3" width="10" height="1"/><rect y="6" width="10" height="1"/></g></svg></div>
  <div class="sortlbl">Sort By</div>
  <div class="select" style="left:106px;width:63px">Position<i></i></div>
  <div class="arrow">↑</div>
  <div class="show">Show</div>
  <div class="select" style="left:293px;width:29px">9<i></i></div>
  <div class="per">per page</div>
  <div class="page">Page:</div><div class="p1">1</div><div class="p2">2</div><div class="next">›</div>
</div>

<article class="abs card" style="left:357px;top:259px">
  <div class="img" role="img" aria-label="Product image"></div>
  <div class="title">SIMPLY DUMMY TEXT OF THE PRINTING</div>
  <div class="bar"><div class="price">$15.00</div><div class="add"><svg width="16" height="12" viewBox="0 0 16 12"><path d="M1 1h2.5l1.8 7h8l1.5-5H4.5" fill="none" stroke="#fff" stroke-width="1.4"/><circle cx="6" cy="10.5" r="1.1" fill="#fff"/><circle cx="12" cy="10.5" r="1.1" fill="#fff"/></svg></div></div>
  <div class="links" style="left:10px">ADD TO COMPARE</div><div class="links" style="right:11px">ADD TO WISHLIST</div>
</article>
<article class="abs card" style="left:601px;top:259px">
  <div class="img" role="img" aria-label="Product image"></div>
  <div class="title">SIMPLY DUMMY TEXT OF THE PRINTING</div>
  <div class="bar"><div class="price">$25.00</div><div class="add"><svg width="16" height="12" viewBox="0 0 16 12"><path d="M1 1h2.5l1.8 7h8l1.5-5H4.5" fill="none" stroke="#fff" stroke-width="1.4"/><circle cx="6" cy="10.5" r="1.1" fill="#fff"/><circle cx="12" cy="10.5" r="1.1" fill="#fff"/></svg></div></div>
  <div class="links" style="left:10px">ADD TO COMPARE</div><div class="links" style="right:11px">ADD TO WISHLIST</div>
</article>
<article class="abs card" style="left:357px;top:575px">
  <div class="img" role="img" aria-label="Product image"></div>
  <div class="title">SIMPLY DUMMY TEXT OF THE PRINTING</div>
  <div class="bar"><div class="price">$30.00</div><div class="add"><svg width="16" height="12" viewBox="0 0 16 12"><path d="M1 1h2.5l1.8 7h8l1.5-5H4.5" fill="none" stroke="#fff" stroke-width="1.4"/><circle cx="6" cy="10.5" r="1.1" fill="#fff"/><circle cx="12" cy="10.5" r="1.1" fill="#fff"/></svg></div></div>
  <div class="links" style="left:10px">ADD TO COMPARE</div><div class="links" style="right:11px">ADD TO WISHLIST</div>
</article>
<article class="abs card" style="left:601px;top:575px">
  <div class="img" role="img" aria-label="Product image"></div>
  <div class="title">SIMPLY DUMMY TEXT OF THE PRINTING</div>
  <div class="bar"><div class="price">$30.00</div><div class="add"><svg width="16" height="12" viewBox="0 0 16 12"><path d="M1 1h2.5l1.8 7h8l1.5-5H4.5" fill="none" stroke="#fff" stroke-width="1.4"/><circle cx="6" cy="10.5" r="1.1" fill="#fff"/><circle cx="12" cy="10.5" r="1.1" fill="#fff"/></svg></div></div>
  <div class="links" style="left:10px">ADD TO COMPARE</div><div class="links" style="right:11px">ADD TO WISHLIST</div>
</article>

<div class="abs toolbar" style="top:875px">
  <div class="view" style="left:0"><svg width="8" height="8"><g fill="#f7c31a"><rect width="3.5" height="3.5"/><rect x="4.5" width="3.5" height="3.5"/><rect y="4.5" width="3.5" height="3.5"/><rect x="4.5" y="4.5" width="3.5" height="3.5"/></g></svg></div>
  <div class="view" style="left:29px"><svg width="10" height="7"><g fill="#888"><rect width="10" height="1"/><rect y="3" width="10" height="1"/><rect y="6" width="10" height="1"/></g></svg></div>
  <div class="sortlbl">Sort By</div>
  <div class="select" style="left:106px;width:63px">Position<i></i></div>
  <div class="arrow">↑</div>
  <div class="show">Show</div>
  <div class="select" style="left:293px;width:29px">9<i></i></div>
  <div class="per">per page</div>
  <div class="page">Page:</div><div class="p1">1</div><div class="p2">2</div><div class="next">›</div>
</div>

<footer class="abs footer">
  <div class="fcol" style="left:108px;top:19px"><h4>Secure Shopping</h4><p>There are many variations of passages of Lorem Ipsum available, but the majority have suffered alteration in some form.</p></div>
  <div class="fcol" style="left:295px;top:19px"><h4>Free Shipping</h4><p>Contrary to popular belief, Lorem Ipsum is not simply random text. It has roots in a piece of classical Latin literature.</p></div>
  <div class="fcol" style="left:480px;top:19px"><h4>Products &amp; Support</h4><p>There are many variations of passages of Lorem Ipsum available, but the majority have suffered alteration in some.</p></div>
  <div class="fcol" style="left:666px;top:19px"><h4>Privacy Policy</h4><p>It is a long established fact that a reader will be distracted by the readable content of a page when looking at.</p></div>
  <div class="fdots"></div>
  <div class="fcol" style="left:108px;top:107px"><h4 style="margin-bottom:2px">Information</h4><ul><li>About US</li><li>Returns policy</li><li>Customer Support</li></ul></div>
  <div class="fcol" style="left:295px;top:107px"><h4 style="margin-bottom:2px">Services &amp; Support</h4><ul><li>Returns policy</li><li>Terms and conditions</li><li>Ssecurity &amp; privacy</li></ul></div>
  <div class="fcol" style="left:480px;top:107px"><h4 style="margin-bottom:4px">Contact Us</h4>
    <div style="font:700 10px Arimo,sans-serif;color:#e59a22;border-bottom:1px dotted #333;width:140px;padding-bottom:5px">+444 (1000) 765432</div>
    <p style="margin-top:6px;padding-left:1px;color:#8a8a8a;line-height:12px;border-bottom:1px dotted #333;width:140px;padding-bottom:22px">Store<br>30 Orchard Row 12.40, Willow Mall<br>GPO 5KT</p>
  </div>
  <div class="fcol" style="left:666px;top:107px;width:160px"><h4>Sign up for our newsletter</h4></div>
  <div class="nl-field"></div>
  <div class="nl-btn"><svg width="14" height="10" viewBox="0 0 14 10"><rect x=".5" y=".5" width="13" height="9" fill="#fff" stroke="#333"/><path d="M.5 .5l6.5 5 6.5-5" fill="none" stroke="#333"/></svg></div>
  <div class="fcol" style="left:666px;top:161px"><h4>Payment Options</h4></div>
  <div class="cards"><i></i><i></i><i></i><i></i><i></i></div>
  <div class="copyright">All Rights Reserved.</div>
</footer>

</body>
</html>
```